Local Flower Farm Needs Business Card Design

I need business cards designed for a flower farm based in Eudora, Kansas.
Business Info:
We are a local cut flower farm located in Eudora, Kansas, founded by Corinne Haldwick. What started as a passion for agriculture and search for more joy in daily life has blossomed into a small business dedicated to providing the community with beautiful, fresh, and sustainable flowers. We specialize in local, seasonal blooms, ensuring that every petal reflects the care and dedication we pour into our craft. Our mission is to deliver the highest quality flowers directly to our customers through local farmers markets and to florists who share our commitment to sustainability. Join us in celebrating the beauty of nature, one bloom at a time!
Contact Details:
Corinne Haldwick
Owner
Phone 913-555-0147
Facebook: Rosalind Thorpe Gardens
Instagram: @RosalindThorpeGardens
Website: RosalindThorpeGardens.example
Target Market(s)
Wholesale to Florists and Direct to Consumer via Farmers Market
Industry/Entity Type
Florist, Farm
Contact Information for Business Card
Name, Contact Info, Logo
Look and feel
Each slider illustrates characteristics of the customer's brand and the style your logo design should communicate.

```html
<!DOCTYPE html>
<html lang="en">
<head>
<meta charset="utf-8">
<title>Rosalind Thorpe Gardens — Business Card</title>
<link rel="stylesheet" href="https://fonts.googleapis.com/css2?family=Crimson+Text:wght@400;700&display=swap">
<style>
  :root {
    --teal-deep: #0b262b;
    --paper: #ffffff;
    --stone: #c4c8cb;
    --ink: #111a1c;
    --backdrop: #e9e9e7;
  }
  * { box-sizing: border-box; margin: 0; padding: 0; }
  html, body { width: 1200px; height: 900px; overflow: hidden; }
  body {
    background: var(--backdrop);
    font-family: "Crimson Text", Georgia, serif;
    position: relative;
  }
  .card {
    position: absolute;
    width: 700px;
    height: 400px;
    box-shadow: 0 10px 28px rgba(0,0,0,0.18);
    overflow: hidden;
  }
  .card--back { left: 110px; top: 40px; background: var(--teal-deep); }
  .card--front { left: 390px; top: 470px; background: var(--paper); }

  .brand-name {
    position: absolute;
    text-align: center;
    font-weight: 400;
    letter-spacing: 0.16em;
    text-transform: uppercase;
    line-height: 1.15;
  }
  .card--back .brand-name {
    left: 0; right: 0; top: 150px;
    font-size: 34px;
    color: var(--paper);
  }
  .card--front .brand-name {
    left: 40px; width: 280px; top: 125px;
    font-size: 26px;
    color: var(--teal-deep);
  }

  .divider {
    position: absolute;
    left: 345px; top: 70px;
    width: 1.5px; height: 180px;
    background: var(--teal-deep);
  }
  .contact {
    position: absolute;
    left: 368px; top: 66px;
    color: var(--ink);
  }
  .contact__name {
    font-size: 27px;
    font-weight: 700;
    color: var(--teal-deep);
    line-height: 1;
  }
  .contact__role { font-size: 19px; margin-top: 4px; }
  .contact__list { list-style: none; margin-top: 18px; }
  .contact__item {
    display: flex; align-items: center; gap: 6px;
    font-size: 19px; line-height: 1.22;
  }
  .contact__icon { width: 14px; height: 14px; flex: none; }
  .contact__mark {
    width: 12px; height: 12px; flex: none;
    background: var(--ink); border-radius: 2px;
  }

  .footer-bands { position: absolute; left: 0; bottom: 0; width: 700px; height: 110px; }
</style>
</head>
<body>

  <section class="card card--back" aria-label="Card back">
    <p class="brand-name">Rosalind Thorpe<br>Gardens</p>
  </section>

  <section class="card card--front" aria-label="Card front">
    <p class="brand-name">Rosalind Thorpe<br>Gardens</p>

    <div class="divider"></div>

    <div class="contact">
      <p class="contact__name">Corinne Haldwick</p>
      <p class="contact__role">Owner</p>
      <ul class="contact__list">
        <li class="contact__item">
          <svg class="contact__icon" viewBox="0 0 16 16" aria-hidden="true">
            <path d="M4 1.5l2.3 2.8-1.4 1.6a9 9 0 0 0 5.2 5.2l1.6-1.4 2.8 2.3-1.6 2.2C7.6 14 2 8.4 1.8 3.1z" fill="var(--ink)"/>
          </svg>
          913-555-0147
        </li>
        <li class="contact__item">
          <svg class="contact__icon" viewBox="0 0 16 16" aria-hidden="true">
            <circle cx="8" cy="8" r="6.5" fill="none" stroke="var(--ink)" stroke-width="1.5"/>
            <ellipse cx="8" cy="8" rx="2.8" ry="6.5" fill="none" stroke="var(--ink)" stroke-width="1.2"/>
            <line x1="1.5" y1="8" x2="14.5" y2="8" stroke="var(--ink)" stroke-width="1.2"/>
          </svg>
          RosalindThorpeGardens.example
        </li>
        <li class="contact__item"><span class="contact__mark"></span>Rosalind Thorpe Gardens</li>
        <li class="contact__item"><span class="contact__mark"></span>@RosalindThorpeGardens</li>
      </ul>
    </div>

    <svg class="footer-bands" viewBox="0 0 700 110" aria-hidden="true">
      <polygon points="0,78 420,78 470,44 470,110 0,110" fill="var(--stone)"/>
      <polygon points="478,44 700,20 700,110 470,110" fill="var(--teal-deep)"/>
    </svg>
  </section>

</body>
</html>
```